Design a modern, classy & professional business card for an online real estate agency, specializing in medium-luxury properties in Thailand and later in Singapore and UK.

Possible design ideas so far: (not essential)

- curved corner(s) to the card, white on front & turquoise on back or visa versa.

- front of card - clear and simple, company name in metallic grey/monochrome, logo graphic & company name on front in spot UV or embossed/debossed effect.

- back of card - large, close-cropped, 'ghost' patterns of the C-shaped curves of logo, or company name repeated on back of card in spot UV.

Target Market(s)

- young to middle-aged professionals mainly (but ideally should design should suit all)

- UK, US,EU,AUS & ASIAN mainly (but ideally should design should suit all countries)

Industry/Entity Type

Real Estate

Requirements
Must have
• THEME:
- Luxurious & Modern
- Clean & striking
- Unique & creative

INFO:
- Logo & company name on front
- Contact details on back:

Tobias Hennlund
Managing Director

www.velmontestates.asia
www.velmontestates.co.uk

Tel: 083-274-6159
email: tobias@velmontestates.asia

(contact details can be displayed in any order as suites design.)

Nice to have
• - curved corner(s) to the card, white on front & turquoise on back or visa versa.

Should not have
• - No generic images of properties, palm trees/coconut trees etc.

- No other other bold colors, except for main turquoise, grey, metallic white & black theme.

- No obvious business card templates

```html
<!DOCTYPE html>
<html lang="en">
<head>
<meta charset="utf-8">
<title>Velmont Estates – Business Card</title>
<link rel="stylesheet" href="https://fonts.googleapis.com/css2?family=Questrial&display=swap">
<style>
  :root{
    --turquoise:#1fc9c6;
    --grey:#7a7a7a;
    --grey-dark:#4a4a4a;
    --text:#2f2f2f;
    --card-light:#ffffff;
    --card-shade:#e4e4e4;
    --backdrop:#ecebe8;
  }
  *{margin:0;padding:0;box-sizing:border-box}
  html,body{width:1200px;height:677px;overflow:hidden;background:var(--backdrop)}
  body{font-family:"Questrial",sans-serif;color:var(--text)}
  .card{
    position:absolute;left:120px;top:64px;width:960px;height:548px;
    border-radius:10px;overflow:hidden;
    background:linear-gradient(115deg,var(--card-light) 0%,var(--card-light) 45%,var(--card-shade) 100%);
    box-shadow:0 18px 40px rgba(0,0,0,.18);
  }
  .card__curves{position:absolute;inset:0}
  .brand{position:absolute;left:120px;top:150px;display:flex;align-items:center;gap:22px}
  .brand__square{width:112px;height:112px;background:var(--turquoise)}
  .brand__name{font-size:58px;color:var(--grey);letter-spacing:1px;line-height:1}
  .person{position:absolute;left:250px;top:300px}
  .person__name{font-size:26px;color:var(--turquoise);letter-spacing:2px;text-transform:uppercase}
  .person__title{font-size:19px;color:var(--grey-dark);margin-top:4px}
  .contact{position:absolute;right:60px;top:128px;text-align:right;font-size:17px;line-height:1.35;color:var(--text)}
  .contact__address{margin-bottom:26px}
  .contact__row{display:flex;justify-content:flex-end;align-items:center;gap:10px;margin-bottom:10px}
  .contact__icon{width:16px;height:16px;flex:none}
  .contact__web{margin-top:18px}
</style>
</head>
<body>
  <div class="card">
    <svg class="card__curves" width="960" height="548" viewBox="0 0 960 548">
      <circle cx="0" cy="455" r="115" fill="none" stroke="var(--turquoise)" stroke-width="46"/>
      <circle cx="455" cy="620" r="190" fill="none" stroke="var(--grey)" stroke-width="50"/>
    </svg>

    <div class="brand">
      <div class="brand__square"></div>
      <div class="brand__name">Velmont Estates</div>
    </div>

    <div class="person">
      <div class="person__name">Tobias Hennlund</div>
      <div class="person__title">Managing Director</div>
    </div>

    <div class="contact">
      <div class="contact__address">042 12th floor/Plaza<br>Riverside Road BKK</div>
      <div class="contact__row">083-274-6159
        <svg class="contact__icon" viewBox="0 0 16 16"><path d="M4 1l3 3-2 2c1 2 3 4 5 5l2-2 3 3-2 3C7 15 1 9 1 3z" fill="var(--turquoise)"/></svg>
      </div>
      <div class="contact__row">tobias@velmontestates.asia
        <svg class="contact__icon" viewBox="0 0 16 16"><rect x="1" y="3" width="14" height="10" rx="1" fill="var(--turquoise)"/><path d="M1 4l7 5 7-5" fill="none" stroke="#fff" stroke-width="1.4"/></svg>
      </div>
      <div class="contact__row contact__web">www.velmontestates.asia
        <svg class="contact__icon" viewBox="0 0 16 16"><circle cx="8" cy="8" r="7" fill="var(--turquoise)"/><path d="M1 8h14M8 1c-3 4-3 10 0 14M8 1c3 4 3 10 0 14" fill="none" stroke="#fff" stroke-width="1"/></svg>
      </div>
      <div class="contact__row">www.velmontestates.co.uk
        <svg class="contact__icon" viewBox="0 0 16 16"><circle cx="8" cy="8" r="7" fill="var(--turquoise)"/><path d="M1 8h14M8 1c-3 4-3 10 0 14M8 1c3 4 3 10 0 14" fill="none" stroke="#fff" stroke-width="1"/></svg>
      </div>
    </div>
  </div>
</body>
</html>
```